Financial Services General Marketing Brochure

Need a brochure to help recipients understand what makes BWC unique and the services that we offer. Must match look/feel of website https://brightwellcustody.example Layouts should make it easy to read the content - content should not be crammed into a traditional size/layout. Please see attached creative brief for specifics.

Target Market(s)

Financial advisors and mature couples looking for trustee services.

Industry/Entity Type

Financial Service

Colors
34a7d8
ffc214

Requirements
Must have
• See Creative Brief

```html
<!DOCTYPE html>
<html lang="en">
<head>
<meta charset="utf-8">
<title>Brightwell Custody – Brochure Spread</title>
<link rel="stylesheet" href="https://fonts.googleapis.com/css2?family=Source+Serif+4:wght@400&family=Open+Sans:ital,wght@0,400;1,400&family=Source+Sans+3:ital,wght@0,600;1,400&display=swap">
<style>
  :root {
    --page: #ffffff;
    --trim: #a9a9a9;
    --heading: #4e7090;
    --body: #555a5f;
    --footer-band: #f5ede5;
    --accent: #f2a12e;
    --overlay: rgba(72, 104, 135, 0.78);
    --white: #ffffff;
  }
  * { margin: 0; padding: 0; box-sizing: border-box; }
  html, body { width: 1200px; height: 1000px; overflow: hidden; background: var(--page); }
  body { position: relative; font-family: "Open Sans", Arial, sans-serif; color: var(--body); }

  .fold-mark { position: absolute; left: 599px; width: 2px; background: var(--trim); }
  .fold-mark--top { top: 180px; height: 20px; }
  .fold-mark--bottom { top: 800px; height: 22px; background: repeating-linear-gradient(var(--trim) 0 6px, transparent 6px 10px); }

  .panel { position: absolute; top: 199px; height: 602px; border: 2px solid var(--trim); overflow: hidden; }
  .panel--inside { left: 0; width: 601px; border-right: none; }
  .panel--cover { left: 599px; width: 601px; border-left: 2px dashed var(--trim); }

  .info-column { position: absolute; left: 36px; top: 34px; width: 230px; }
  .info-block { margin-bottom: 0; }
  .info-block h2 {
    font-family: "Source Serif 4", Georgia, serif; font-weight: 400;
    font-size: 22px; color: var(--heading); line-height: 1.1; letter-spacing: 0.2px;
  }
  .info-block .lead { font-style: italic; font-size: 9px; line-height: 13px; margin-top: 4px; }
  .info-block ul { list-style: none; margin-top: 12px; }
  .info-block li { font-size: 9.5px; line-height: 13px; padding-left: 14px; position: relative; }
  .info-block li::before { content: "•"; position: absolute; left: 4px; color: #8a8f94; }
  .plain-list { font-size: 9.5px; line-height: 13px; margin-top: 4px; }
  .block-offer { height: 91px; }
  .block-serve { height: 101px; }
  .block-how { height: 193px; }

  .photo { position: absolute; }
  .photo--consult {
    left: 279px; top: 0; width: 322px; height: 514px;
    background: linear-gradient(160deg, #f3f4f6 0%, #d9dde2 30%, #6f87a6 55%, #2c3f63 75%, #b9b2a6 100%);
  }
  .photo--family {
    left: 0; top: 0; width: 601px; height: 602px;
    background: linear-gradient(180deg, #8c9a63 0%, #b4b48a 25%, #d7c9b8 45%, #9aa77a 80%, #7d9b44 100%);
  }

  .contact-band {
    position: absolute; left: 279px; top: 514px; width: 322px; height: 88px;
    background: var(--footer-band); display: flex; align-items: center;
  }
  .brand { display: flex; align-items: center; gap: 8px; font-family: "Source Sans 3", Arial, sans-serif; font-weight: 600; }
  .brand-dot { border-radius: 50%; background: var(--accent); flex: none; }
  .brand--small { margin-left: 18px; width: 128px; color: var(--heading); font-size: 13px; line-height: 14px; }
  .brand--small .brand-dot { width: 22px; height: 22px; }
  .band-divider { width: 1px; height: 52px; background: var(--accent); margin: 0 10px 0 4px; }
  .contact-list { font-size: 10px; line-height: 14px; color: var(--body); list-style: none; }

  .tagline-band {
    position: absolute; left: 0; top: 343px; width: 601px; height: 209px;
    background: var(--overlay); display: flex; align-items: center;
  }
  .tagline {
    margin-left: 17px; width: 310px; color: var(--white);
    font-family: "Source Sans 3", Arial, sans-serif; font-style: italic; font-size: 19px; line-height: 24px;
  }
  .tagline-divider { width: 1px; height: 42px; background: rgba(255,255,255,0.7); margin: 0 24px 0 11px; }
  .brand--large { color: var(--white); font-size: 22px; line-height: 22px; width: 230px; }
  .brand--large .brand-dot { width: 40px; height: 40px; }
</style>
</head>
<body>
  <div class="fold-mark fold-mark--top"></div>
  <div class="fold-mark fold-mark--bottom"></div>

  <section class="panel panel--inside">
    <div class="info-column">
      <div class="info-block block-offer">
        <h2>What We Offer</h2>
        <p class="lead">We specialize exclusively in the delivery of trustee and estate fiduciary services.</p>
      </div>
      <div class="info-block block-serve">
        <h2>Who We Serve</h2>
        <p class="plain-list">Families<br>Professional Advisors<br>Foundations</p>
      </div>
      <div class="info-block block-how">
        <h2>How We Serve</h2>
        <p class="lead">Our expertise and experience is in family wealth.<br>In this regard, we serve in the following ways:</p>
        <ul>
          <li>Trustee (Trusts)</li>
          <li>Executor and Personal Representative (Will)</li>
          <li>Agent for Financial Affairs (Power of Attorney)</li>
          <li>Trust Protector</li>
          <li>Special Independent Trustee</li>
          <li>Consultant</li>
          <li>Expert Witness</li>
        </ul>
      </div>
      <div class="info-block">
        <h2>Trust Specialties</h2>
        <p class="lead">The general types of trusts on which we serve as trustee:</p>
        <ul>
          <li>Family Trusts</li>
          <li>Charitable Trusts</li>
          <li>Family Foundations</li>
          <li>Life Insurance Trusts</li>
          <li>Retirement Trusts</li>
          <li>Special Needs Trusts</li>
        </ul>
      </div>
    </div>

    <div class="photo photo--consult" role="img" aria-label="Photo of a smiling senior couple meeting with an advisor to review documents"></div>

    <div class="contact-band">
      <div class="brand brand--small"><span class="brand-dot"></span><span>Brightwell Custody</span></div>
      <div class="band-divider"></div>
      <ul class="contact-list">
        <li>brightwellcustody.example</li>
        <li>555-014-2290</li>
        <li>info@brightwellcustody.example</li>
      </ul>
    </div>
  </section>

  <section class="panel panel--cover">
    <div class="photo photo--family" role="img" aria-label="Photo of a happy multi-generational family sitting together outdoors on the grass"></div>
    <div class="tagline-band">
      <p class="tagline">Helping families protect and enrich a multi-generational heritage</p>
      <div class="tagline-divider"></div>
      <div class="brand brand--large"><span class="brand-dot"></span><span>Brightwell Custody</span></div>
    </div>
  </section>
</body>
</html>
```